Los Angeles based Demolition, Grading, and Structural concrete Contractor in need of a Sale brochure

We are a Los Angeles-based demolition, grading, and structural concrete contractor looking for a professionally designed sales brochure that represents our company and services. The brochure should be visually appealing, easy to read, and include the following:

-Company Logo: Prominently displayed to enhance brand identity.

-Services We Offer: A clear breakdown of our key services, including demolition, grading, and structural concrete work.

-Project Scope & Capabilities: A brief explanation of the type of projects we handle (residential, commercial, industrial).

-Pricing Information: Mention that demolition services start at $20,000. This price includes complete demolition of structure, safe debris removal and hauling, site preparation for new construction.

-Contact Information: Our phone number(818.502.6617), email(contact@brovanbuildersinc.example) , and website for potential clients to reach out.

The design should reflect the professionalism and strength of our industry, using a modern, clean layout with bold colors that align with construction and demolition themes. Images of past work or stock photos representing our services are encouraged.

Final deliverables should be print-ready (PDF) and digital-friendly formats. Looking forward to creative and impactful designs!

```html
<!DOCTYPE html>
<html lang="en">
<head>
<meta charset="utf-8">
<title>Brovan Builders – Sales Flyer</title>
<link href="https://fonts.googleapis.com/css2?family=Oswald:wght@500;600;700&family=Roboto:wght@400;500&display=swap" rel="stylesheet">
<style>
  :root {
    --blue: #1b75c2;
    --teal: #1d8fc0;
    --brown: rgba(74, 58, 40, 0.9);
    --sand: #b99a72;
    --sand-light: #c6a87f;
    --dark: #37383b;
    --grey: #6e6f72;
    --ink: #111318;
    --white: #ffffff;
    --page: #d4d4d4;
    --photo-demo: #8a8a6a;
    --photo-grade: #b4a688;
    --photo-concrete: #a3a39e;
  }
  * { margin: 0; padding: 0; box-sizing: border-box; }
  html, body { width: 714px; height: 1200px; overflow: hidden; background: var(--page); }
  body { font-family: "Roboto", Arial, sans-serif; color: var(--ink); }
  .flyer { position: absolute; left: 0; top: 132px; width: 714px; height: 935px; background: var(--white); overflow: hidden; }
  .display { font-family: "Oswald", "Arial Narrow", sans-serif; font-weight: 600; }

  /* Hero */
  .hero { position: absolute; left: 0; top: 0; width: 714px; height: 342px; }
  .hero-photo { position: absolute; inset: 0; background: linear-gradient(135deg, var(--sand-light), var(--sand)); }
  .hero-panel { position: absolute; inset: 0; }
  .brand { position: absolute; left: 43px; top: 16px; display: flex; align-items: center; gap: 8px; color: var(--white); font-family: "Oswald", sans-serif; font-weight: 600; font-size: 22px; letter-spacing: 1px; }
  .brand-mark { width: 16px; height: 16px; background: var(--blue); }
  .hero-title { position: absolute; left: 43px; top: 78px; width: 330px; color: var(--white); font-size: 38px; line-height: 43px; }
  .hero-copy { position: absolute; left: 43px; top: 218px; width: 258px; color: var(--white); font-size: 13px; line-height: 16.5px; }

  /* Services */
  .services-band { position: absolute; left: 0; top: 342px; width: 714px; height: 84px; background: var(--blue); }
  .services-title { position: absolute; left: 0; top: 348px; width: 714px; text-align: center; color: var(--white); font-size: 40px; line-height: 52px; }
  .services-ground { position: absolute; left: 0; top: 426px; width: 714px; height: 192px; background: var(--dark); }
  .service { position: absolute; top: 411px; width: 201px; color: var(--white); }
  .service-photo { width: 201px; height: 130px; }
  .service-photo.demolition { background: var(--photo-demo); }
  .service-photo.grading { background: var(--photo-grade); }
  .service-photo.concrete { background: var(--photo-concrete); }
  .service-name { margin-top: 16px; font-size: 19px; line-height: 22px; }
  .service-copy { margin-top: 3px; font-size: 10px; line-height: 12.5px; color: #e4e4e4; }

  /* Info */
  .info-heading { position: absolute; top: 652px; font-size: 21px; line-height: 26px; color: var(--ink); }
  .info-rule { position: absolute; top: 686px; width: 96px; height: 3px; background: var(--blue); }
  .price-line { position: absolute; left: 43px; top: 700px; font-size: 17px; line-height: 22px; }
  .checklist { position: absolute; left: 43px; top: 731px; list-style: none; font-size: 13px; font-weight: 500; }
  .checklist li { display: flex; align-items: center; gap: 8px; height: 22.5px; }
  .scope-copy { position: absolute; left: 363px; top: 705px; width: 305px; font-size: 10.5px; line-height: 15.3px; }

  /* Footer */
  .footer { position: absolute; left: 0; top: 836px; width: 714px; height: 99px; }
  .call { position: absolute; left: 43px; top: 16px; color: var(--white); font-size: 22px; line-height: 26px; }
  .contact { position: absolute; right: 43px; top: 34px; text-align: right; color: var(--white); font-size: 14px; line-height: 25px; }
</style>
</head>
<body>
<main class="flyer">
  <section class="hero">
    <div class="hero-photo" role="img" aria-label="Photo of a red compact excavator working on a graded dirt site"></div>
    <svg class="hero-panel" width="714" height="342" viewBox="0 0 714 342" aria-hidden="true">
      <polygon points="0,0 408,0 311,342 0,342" fill="var(--brown)"/>
      <polygon points="408,0 428,0 331,342 311,342" fill="var(--teal)"/>
    </svg>
    <div class="brand"><span class="brand-mark"></span>BROVAN</div>
    <h1 class="hero-title display">Built for Strength, Engineered for Success</h1>
    <p class="hero-copy">Brovan Builders Inc. is a trusted demolition, grading, and structural concrete contractor serving Los Angeles and beyond. With years of experience in the industry, we bring precision, efficiency, and safety to every project—whether residential, commercial, or industrial.</p>
  </section>

  <div class="services-band"></div>
  <h2 class="services-title display">Our Services</h2>
  <div class="services-ground"></div>

  <article class="service" style="left:43px">
    <div class="service-photo demolition" role="img" aria-label="Photo of a yellow excavator demolishing a structure among trees"></div>
    <h3 class="service-name display">Demolition</h3>
    <p class="service-copy">Safe, efficient, and complete structure removal, including debris hauling.</p>
  </article>
  <article class="service" style="left:256px">
    <div class="service-photo grading" role="img" aria-label="Photo of a graded building pad beside a retaining wall"></div>
    <h3 class="service-name display">Grading</h3>
    <p class="service-copy">Site preparation for new builds, leveling, excavation, and soil stabilization.</p>
  </article>
  <article class="service" style="left:470px">
    <div class="service-photo concrete" role="img" aria-label="Photo of poured concrete foundations on a hillside site"></div>
    <h3 class="service-name display">Structural Concrete</h3>
    <p class="service-copy">Foundations, retaining walls, slabs, and reinforced concrete work.</p>
  </article>

  <h2 class="info-heading display" style="left:43px">Transparent Pricing</h2>
  <div class="info-rule" style="left:43px"></div>
  <p class="price-line display">Demolition services start at $20,000</p>
  <ul class="checklist">
    <li><svg width="16" height="13" viewBox="0 0 16 13" aria-hidden="true"><path d="M1.5 7 L6 11 L14.5 1.5" fill="none" stroke="var(--blue)" stroke-width="3"/></svg>Complete structure removal</li>
    <li><svg width="16" height="13" viewBox="0 0 16 13" aria-hidden="true"><path d="M1.5 7 L6 11 L14.5 1.5" fill="none" stroke="var(--blue)" stroke-width="3"/></svg>Safe debris removal &amp; hauling</li>
    <li><svg width="16" height="13" viewBox="0 0 16 13" aria-hidden="true"><path d="M1.5 7 L6 11 L14.5 1.5" fill="none" stroke="var(--blue)" stroke-width="3"/></svg>Site preparation for new construction</li>
  </ul>

  <h2 class="info-heading display" style="left:363px">Project Scope &amp; Capabilities</h2>
  <div class="info-rule" style="left:363px"></div>
  <p class="scope-copy">We handle projects of all sizes, from small-scale residential demolitions to large commercial and industrial site preparations. Our skilled team ensures compliance with local regulations and industry best practices, delivering quality work on time and within budget.</p>

  <footer class="footer">
    <svg width="714" height="99" viewBox="0 0 714 99" style="position:absolute;inset:0" aria-hidden="true">
      <rect width="714" height="99" fill="var(--grey)"/>
      <polygon points="0,0 270,0 244,99 0,99" fill="var(--white)"/>
      <polygon points="0,0 262,0 236,99 0,99" fill="var(--blue)"/>
    </svg>
    <p class="call display">Call Us<br>818.502.6617</p>
    <p class="contact">contact@brovanbuildersinc.example<br>www.brovanbuildersinc.example</p>
  </footer>
</main>
</body>
</html>
```